Bramblewick Forage Business Cards

I need a business card with my logo, number, Facebook account, and some information about what I am selling. Green card with logo on the front. 555-214-8392 phone number, @bramblewickforage Facebook, •Orchardgrass Hay •Alfalfa Hay •Mixed Grass Hay , and “Premium Quality Hay” all written on the back.

Target Market(s)

Hay

Contact Information for Business Card

Phone number, Facebook, different types of hay.

Colors
00AB8E
00BBA5
67D7C9
C6EFE9
E9F9F6

```html
<!DOCTYPE html>
<html lang="en">
<head>
<meta charset="utf-8">
<title>Bramblewick Forage Business Cards</title>
<link rel="stylesheet" href="https://fonts.googleapis.com/css2?family=Arimo:wght@400;700&family=Yellowtail&display=swap">
<style>
  :root {
    --backdrop: #1c1c1c;
    --card-white: #f4f4f2;
    --card-green: #00a349;
    --green-deep: #067a37;
    --green-mark: #19a548;
    --ink: #2a2a2a;
    --rule: #555555;
    --white: #ffffff;
  }
  * { margin: 0; padding: 0; box-sizing: border-box; }
  html, body { width: 1200px; height: 963px; overflow: hidden; }
  body {
    background: var(--backdrop);
    font-family: "Arimo", Arial, sans-serif;
    display: flex;
    flex-direction: column;
    align-items: center;
    justify-content: center;
    gap: 40px;
  }
  .card {
    width: 760px;
    height: 434px;
    border-radius: 26px;
    position: relative;
    overflow: hidden;
  }

  /* Front */
  .card-front { background: var(--card-white); }
  .front-brand {
    position: absolute;
    left: 64px;
    top: 120px;
    display: flex;
    align-items: center;
    gap: 14px;
  }
  .brand-dot {
    width: 46px;
    height: 46px;
    border-radius: 50%;
    background: var(--green-mark);
  }
  .brand-name {
    font-weight: 700;
    font-size: 27px;
    color: var(--ink);
  }
  .front-divider {
    position: absolute;
    left: 392px;
    top: 150px;
    width: 1px;
    height: 150px;
    background: var(--rule);
  }
  .front-contact {
    position: absolute;
    left: 420px;
    top: 150px;
  }
  .person-name {
    font-family: "Yellowtail", cursive;
    font-size: 44px;
    color: var(--green-mark);
    line-height: 1;
  }
  .person-role {
    font-size: 19px;
    color: var(--ink);
    margin-top: 4px;
  }
  .contact-list {
    list-style: none;
    margin-top: 22px;
    display: flex;
    flex-direction: column;
    gap: 12px;
  }
  .contact-item {
    display: flex;
    align-items: center;
    gap: 12px;
    font-size: 20px;
    color: var(--ink);
  }
  .contact-icon { width: 20px; height: 20px; flex: none; }
  .social-square {
    width: 18px;
    height: 18px;
    border-radius: 4px;
    background: var(--green-mark);
    flex: none;
    margin: 0 1px;
  }

  /* Back */
  .card-back {
    background: var(--card-green);
    display: flex;
    flex-direction: column;
    align-items: center;
    justify-content: center;
  }
  .back-brand {
    display: flex;
    align-items: center;
    gap: 16px;
  }
  .back-brand .brand-dot {
    width: 58px;
    height: 58px;
    background: var(--green-deep);
  }
  .back-brand .brand-name {
    font-size: 38px;
    color: var(--green-deep);
  }
  .hay-list {
    list-style: none;
    display: flex;
    gap: 18px;
    margin-top: 46px;
    font-weight: 700;
    font-size: 21px;
    color: var(--white);
  }
  .hay-list li::before { content: "\2022\00a0"; }
  .tagline {
    font-family: "Yellowtail", cursive;
    font-size: 32px;
    color: var(--white);
    margin-top: 10px;
  }
</style>
</head>
<body>
  <section class="card card-front">
    <div class="front-brand">
      <span class="brand-dot"></span>
      <span class="brand-name">Bramblewick Forage</span>
    </div>
    <div class="front-divider"></div>
    <div class="front-contact">
      <p class="person-name">Dale Harrow</p>
      <p class="person-role">Owner</p>
      <ul class="contact-list">
        <li class="contact-item">
          <svg class="contact-icon" viewBox="0 0 24 24" aria-hidden="true">
            <path fill="#19a548" d="M6.6 10.8a15.1 15.1 0 0 0 6.6 6.6l2.2-2.2a1 1 0 0 1 1-.25 11.4 11.4 0 0 0 3.6.57 1 1 0 0 1 1 1V20a1 1 0 0 1-1 1A17 17 0 0 1 3 4a1 1 0 0 1 1-1h3.5a1 1 0 0 1 1 1c0 1.25.2 2.45.57 3.57a1 1 0 0 1-.25 1z"/>
          </svg>
          555-214-8392
        </li>
        <li class="contact-item">
          <span class="social-square"></span>
          @bramblewickforage
        </li>
      </ul>
    </div>
  </section>

  <section class="card card-back">
    <div class="back-brand">
      <span class="brand-dot"></span>
      <span class="brand-name">Bramblewick Forage</span>
    </div>
    <ul class="hay-list">
      <li>Orchardgrass Hay</li>
      <li>Alfalfa Hay</li>
      <li>Mixed Grass Hay</li>
    </ul>
    <p class="tagline">Premium Quality Hay</p>
  </section>
</body>
</html>
```